SEO Agentur www.klickretter.de - Webseite soll neu designed werden (Start- und Unterseite)
Zielgruppe
Alle Infos sind auf der Seite www.klickretter.de enthalten.
Aufgabenstellung
Die Seite soll neu gestalltet werden. Wir möchten gerne ein wenig professioneller werden. Der Name der Seite zwingt uns allerdings ein gewisses Thema auf.
Die Aufgabe:
Ein professionelleres Design der Startseite und einer Unterseite. Die Programmierung machen wir selbst. Thema Suche und Helden muss bleiben aufgrund der URL.
Mit dem Gewinner würden wir dann auch geren jedes Element der Seite durchgehen und neu gestallten (separater Auftrag).
Das Blitzwolf Logo ist aufgrund des neuen Films auch gewaltiger und seriöser geworden. Vielleicht kann man daran anknüpfen. Ist aber keine Bedingung nur eine kleine Idee.
Wir werden alle Vorschläge ca. 50 Leuten vorstellen und dann den Vorschlag mit den meisten Stimmen wählen.

```html
<!DOCTYPE html>
<html lang="de">
<head>
<meta charset="utf-8">
<title>Klickretter.de – SEO Agentur</title>
<link href="https://fonts.googleapis.com/css2?family=Arimo:wght@400;700&display=swap" rel="stylesheet">
<style>
:root{
  --red:#d0000b;
  --text:#8c8c8c;
  --dark:#333;
  --nav-bg:#f1f1f1;
  --band:#f0f0f0;
  --footer:#8a8a8a;
  --footer-bottom:#ececec;
  --white:#fff;
  --line:#d6d6d6;
  --step:#e6e6ec;
  --step-top:#f6f6f9;
  --step-side:#d4d4dc;
}
*{margin:0;padding:0;box-sizing:border-box}
html,body{width:1200px;height:1079px;overflow:hidden}
body{position:relative;font-family:"Arimo",Arial,sans-serif;color:var(--text);background:var(--white);font-size:8.4px;line-height:10.6px}
.abs{position:absolute}
/* header */
.topbar{left:0;top:0;width:1200px;height:47px;background:var(--nav-bg);border-bottom:1px solid #e2e2e2;z-index:2}
.brand{left:300px;top:16px;display:flex;align-items:center;gap:5px;font-size:10px;font-weight:700;color:var(--red);z-index:3}
.brand-dot{width:12px;height:12px;border-radius:50%;background:var(--red)}
.nav{left:499px;top:18px;font-size:8.4px;color:#777;z-index:3}
.nav span{position:absolute;white-space:nowrap}
.nav .active{color:var(--red)}
.nav-underline{left:499px;top:45px;width:30px;height:2px;background:var(--red);z-index:3}
.drop-underline{left:599px;top:45px;width:76px;height:2px;background:var(--red);z-index:3}
.dropdown{left:599px;top:47px;width:122px;background:var(--white);border:1px solid #ccc;box-shadow:0 1px 3px rgba(0,0,0,.2);z-index:5}
.dropdown div{height:18.8px;line-height:18.8px;padding-left:6px;font-size:8.3px;color:#888;border-bottom:1px solid #e8e8e8}
.dropdown div:last-child{border-bottom:none}
/* hero */
.hero{left:0;top:47px;width:1200px;height:316px;background:var(--white)}
.hero-title{left:0;top:84px;width:1200px;text-align:center;font-size:15px;line-height:18px;font-weight:400;color:#666;letter-spacing:.3px}
.hero-text{left:488px;top:107px;width:380px;text-align:center;font-size:8.4px;line-height:10.4px;color:#999}
.hero-rule{left:0;top:363px;width:1200px;height:3px;background:#d9d9de}
/* features */
.band{left:0;top:366px;width:1200px;height:322px;background:var(--band)}
.feature{width:190px;text-align:center}
.feature h3{font-weight:400;color:var(--red);font-size:9.4px;line-height:12px;height:24px;display:flex;align-items:flex-end;justify-content:center}
.feature .pic{width:169px;height:133px;margin:10px auto 0;border:1px solid #bbb}
.feature p{margin:14px auto 0;width:150px;color:#999;height:52px;font-size:8.2px;line-height:10.5px}
.btn{display:inline-block;margin-top:12px;width:81px;height:19px;line-height:19px;background:var(--red);color:var(--white);font-size:8.6px;font-weight:700}
.vrule{width:1px;background:var(--line)}
/* info */
.info h2{font-size:11px;line-height:13px;font-weight:700;color:var(--red)}
.info p{color:var(--text)}
.info em{font-style:normal;color:var(--red)}
.info strong{font-weight:700;color:var(--dark)}
/* footer */
.footer{left:0;top:903px;width:1200px;height:159px;background:var(--footer);border-top:2px solid #bdbdbd}
.fcol{color:#f2f2f2;font-size:8.4px;line-height:10.6px}
.fcol h4{font-size:8.4px;font-weight:700;color:var(--white);margin-bottom:9px}
.copy{left:0;top:1062px;width:1200px;height:17px;background:var(--footer-bottom);text-align:center;line-height:17px;font-size:7px;color:#888}
</style>
</head>
<body>

<header>
  <div class="abs topbar"></div>
  <div class="abs brand"><span class="brand-dot"></span>Klickretter.de</div>
  <nav class="abs nav">
    <span class="active" style="left:3px">Ablauf</span>
    <span style="left:45px">Ihre Vorteile</span>
    <span style="left:109px">Leistungen ⌄</span>
    <span style="left:178px">100% Garantie</span>
    <span style="left:254px">Infos</span>
    <span style="left:300px">Blog</span>
    <span style="left:334px">Kontakt</span>
    <span style="left:388px">
      <svg width="10" height="10" viewBox="0 0 10 10"><circle cx="4" cy="4" r="3" fill="none" stroke="#999" stroke-width="1.2"/><line x1="6.2" y1="6.2" x2="9.5" y2="9.5" stroke="#999" stroke-width="1.5"/></svg>
    </span>
  </nav>
  <div class="abs nav-underline"></div>
  <div class="abs drop-underline"></div>
  <div class="abs dropdown">
    <div>Suchmaschinenoptimierung</div>
    <div>Homepageerstellung</div>
    <div>Suchmaschinenwerbung</div>
    <div>Social Media</div>
    <div>Findora Penalty</div>
    <div>Erklärvideos</div>
  </div>
</header>

<section>
  <svg class="abs hero" width="1200" height="316" viewBox="0 0 1200 316" role="img" aria-label="Geschäftsleute stehen auf ansteigenden weißen Treppenstufen">
    <defs>
      <linearGradient id="stepFace" x1="0" y1="0" x2="0" y2="1">
        <stop offset="0" stop-color="#eeeef3"/>
        <stop offset="1" stop-color="#dedee6"/>
      </linearGradient>
    </defs>
    <g fill="url(#stepFace)" stroke="#f8f8fb" stroke-width="1">
      <rect x="0" y="297" width="63" height="19"/>
      <rect x="63" y="290" width="44" height="26"/>
      <rect x="106" y="279" width="63" height="37"/>
      <rect x="169" y="294" width="44" height="22"/>
      <rect x="212" y="234" width="57" height="82"/>
      <rect x="269" y="209" width="53" height="107"/>
      <rect x="322" y="162" width="66" height="154"/>
      <rect x="387" y="219" width="44" height="97"/>
      <rect x="431" y="177" width="63" height="139"/>
      <rect x="494" y="265" width="56" height="51"/>
      <rect x="550" y="290" width="50" height="26"/>
      <rect x="600" y="281" width="62" height="35"/>
      <rect x="662" y="290" width="44" height="26"/>
      <rect x="706" y="262" width="63" height="54"/>
      <rect x="769" y="237" width="44" height="79"/>
      <rect x="812" y="231" width="63" height="85"/>
      <rect x="875" y="203" width="50" height="113"/>
      <rect x="925" y="179" width="56" height="137"/>
      <rect x="981" y="156" width="56" height="160"/>
      <rect x="1037" y="178" width="50" height="138"/>
      <rect x="1087" y="122" width="50" height="194"/>
      <rect x="1137" y="62" width="63" height="254"/>
    </g>
    <g fill="var(--step-side)">
      <rect x="0" y="297" width="3" height="19"/>
      <rect x="212" y="234" width="3" height="82"/>
      <rect x="322" y="162" width="3" height="154"/>
      <rect x="431" y="177" width="3" height="139"/>
      <rect x="706" y="262" width="3" height="54"/>
      <rect x="875" y="203" width="3" height="113"/>
      <rect x="981" y="156" width="3" height="160"/>
      <rect x="1087" y="122" width="3" height="194"/>
      <rect x="1137" y="62" width="3" height="254"/>
    </g>
  </svg>
  <h1 class="abs hero-title">SEO MIT DEN RETTER-HELDEN</h1>
  <p class="abs hero-text">Wir von Klickretter.de haben uns auf die Optimierung Ihrer Website spezialisiert.<br>Wir helfen Ihnen, dass Sie in den Suchergebnissen ganz vorne gerankt<br>werden. Mit unserer Hilfe steigern Sie Besucherzahlen, Ihre Kundenzahlen,<br>Ihr Image und Ihre Umsätze. Bei uns erhalten<br>Sie alles aus einer Hand.</p>
  <div class="abs hero-rule"></div>
</section>

<section>
  <div class="abs band"></div>
  <div class="abs vrule" style="left:486px;top:417px;height:208px"></div>
  <div class="abs vrule" style="left:690px;top:417px;height:208px"></div>

  <div class="abs feature" style="left:289px;top:387px">
    <h3>Was ist<br>Suchmaschinenoptimierung (SEO)?</h3>
    <div class="pic" role="img" aria-label="Hand zeichnet SEO-Schema mit Begriffen wie Content und Keywords" style="background:linear-gradient(135deg,#fff 55%,#f3e3d8 100%)"></div>
    <p>Kurz gesagt: Mehr Kunden und mehr Umsatz! Unter dem Begriff SEO versteht sich ein technischer Prozess der Ihnen zu einer nachhaltigen Verbesserung bei den ...</p>
    <span class="btn">Hier Weiterlesen</span>
  </div>

  <div class="abs feature" style="left:493px;top:387px">
    <h3>SEO (organisch)</h3>
    <div class="pic" role="img" aria-label="SEO-Kreislauf mit Symbolen für Analyse, Links und Content" style="background:radial-gradient(circle,#e8f3e8 0%,#fff 60%)"></div>
    <p style="margin-top:12px">Suchmaschinenoptimierung ist die effizienteste und günstigste Art, im Internet neue Kunden zu bekommen. Wir von Klickretter.de positionieren ausgewä...</p>
    <span class="btn" style="margin-top:14px">Hier Weiterlesen</span>
  </div>

  <div class="abs feature" style="left:697px;top:387px">
    <h3>Unsere Garantie für Sie:</h3>
    <div class="pic" role="img" aria-label="Daumen nach oben aus SEO-Begriffen als Wortwolke" style="background:radial-gradient(circle,#9a9a9a 0%,#dcdcdc 45%,#fff 70%)"></div>
    <p style="margin-top:10px">Sollten Ihre vorab festgelegten Suchbegriffe gegen alle Erwartungen nicht innerhalb von 6 Monaten unter den TOP 10 bei den Suchergebnissen von Findora gelistet sein ...</p>
    <span class="btn" style="margin-top:16px">Hier Weiterlesen</span>
  </div>
</section>

<section class="info">
  <h2 class="abs" style="left:310px;top:718px">Wieso brauchen Sie SEO?</h2>
  <div class="abs" style="left:302px;top:742px;width:292px">
    <p>Durch neue Kunden im Internet wächst Ihr Unternehmen stabil, nachhaltig und kontrolliert. Mit Hilfe unserer Dienstleistung kommen Sie auf <em>die ersten Plätze bei Findora &amp; Co.</em> und bleiben dort auch langfristig. Durch unsere Arbeit erhalten Sie mehr Besucher, mehr Kunden und folglich mehr Umsatz! Bereits einer unseren ersten Kunden (ein mittelständischer Werkzeughandel aus Kassel) hat dank unserer Hilfe bereits nach 6 Monaten mit seinem Onlineshop eine <em>monatliche Umsatzsteigerung von ca. 50%</em>. Diese Umsatzsteigerung ist ausschließlich auf unserer Maßnahmen zurückzuführen.</p>
    <p style="margin-top:7px">Lassen Sie das Internet nicht links liegen! Fordern Sie jetzt ein <em style="font-weight:700">kostenloses Angebot</em> für Ihre Optimierung an!</p>
  </div>

  <div class="abs vrule" style="left:607px;top:731px;height:141px"></div>

  <h2 class="abs" style="left:629px;top:718px">Erfolgsbasiert und mit 100% Geld zurück Garantie</h2>
  <div class="abs" style="left:621px;top:742px;width:195px;color:var(--dark)">
    <span style="white-space:nowrap">Wir halten was wir versprechen – GARANTIERT!</span><br>Als einer der wenigen Anbieter geben wir<br>Ihnen eine 100% Geld-Zurück-Garantie,<br>sofern wir Ihre Ziele nicht erreichen.
  </div>
  <div class="abs" style="left:621px;top:806px;width:260px">
    <p>Kontaktieren Sie uns und fordern Sie<br>jetzt gleich ein <strong>kostenloses Angebot</strong> an!<br>Gemeinsam legen wir mit Ihnen zusammen<br>Ihre Ziele fest, damit sich Ihre Website bei Findora<br>&amp; Co. in den Suchergebnissen ganz oben befindet - garantiert.</p>
  </div>
  <div class="abs" style="left:806px;top:754px;width:62px;height:62px;border-radius:50%;background:#2a6fcf" aria-hidden="true"></div>
</section>

<footer>
  <div class="abs footer"></div>
  <div class="abs fcol" style="left:300px;top:920px">
    <h4>Menü</h4>
    Ablauf<br>Ihre Vorteile<br>Unsere Leistungen<br>100% Geld-zurück-Garantie<br>Infos<br>Blog<br>Kontakt
  </div>
  <div class="abs fcol" style="left:449px;top:920px">
    <h4>Suchmaschinenoptimierung</h4>
    SEO Agentur<br>SEO Marketing<br>SEO Umstaz<br>SEO Agentur Erf olgsbasiert<br>Suchmaschinenoptimierung Agentur
  </div>
  <div class="abs fcol" style="left:635px;top:920px">
    <h4>Suchmaschinenwerbung</h4>
    AdPilot Agentur<br>Findora AdPilot<br>SEA Agentur<br>SEM Agentur
  </div>
  <div class="abs fcol" style="left:802px;top:920px">
    <h4>Kontaktdaten</h4>
    Klickretter.de GbR<br>Lindenweg 12<br>49086 Musterstadt<br><br>Impressum<br>Zum Kontaktformular<br><br>0541 - 555 012 34<br>Wir warten auf Ihren Anruf
  </div>
  <div class="abs copy">Copyright © 2014 Klickretter.de</div>
</footer>

</body>
</html>
```